National online rug retailer needs a home page design

See the FloorNest logo and create a home page design around that color theme. Details are spelled out in word document uploaded below.

Apparently this website did not take my attachement showing the logo and basic requirements.  If you would send me your email address, I will send you the attachment directly.
Best regards,
Tom Vance
tvance@mrdcorp.example

Target Market(s)

The target market is home owners 25 to 75 years old with combined incomes over $100,000 per year.

Industry/Entity Type

Online

Requirements
Must have
• Lots of white space with black letters and creative use of red and possibly one other color. Would like a compelling call to action button.

```html
<!DOCTYPE html>
<html lang="en">
<head>
<meta charset="utf-8">
<title>FloorNest – Home</title>
<link href="https://fonts.googleapis.com/css2?family=Gudea:wght@400;700&family=Open+Sans:wght@400;600;700&display=swap" rel="stylesheet">
<style>
:root{
  --red:#e30613;
  --red-dark:#c20510;
  --ink:#1b1b1b;
  --text:#555;
  --muted:#888;
  --line:#dcdcdc;
  --nav:#3f3f3f;
  --panel:#f1f1f1;
  --dark:#454545;
  --white:#fff;
}
*{box-sizing:border-box;margin:0;padding:0}
html,body{width:780px;height:1200px;overflow:hidden;background:var(--white)}
body{position:relative;font-family:"Open Sans",sans-serif;color:var(--text);font-size:8px}
.abs{position:absolute}
a{color:inherit;text-decoration:none}

/* header */
.brand{left:84px;top:16px;display:flex;align-items:center;gap:6px}
.brand-mark{width:24px;height:24px;background:var(--red)}
.brand-name{font-family:"Gudea",sans-serif;font-size:26px;color:var(--red);font-weight:400;line-height:1}
.brand-tag{left:142px;top:54px;font-size:7px;color:var(--muted)}
.search{left:316px;top:29px;width:148px;height:24px;display:flex}
.search input{flex:1;border:1px solid #ccc;font:7px "Open Sans",sans-serif;padding:0 6px;color:#999}
.search button{width:23px;border:0;background:#666;display:flex;align-items:center;justify-content:center}
.util{right:86px;top:17px;text-align:right;font-size:7.5px;color:#666;line-height:1}
.util .tel{font-size:11px;color:#666;margin:8px 0 9px}
.util .tel b{color:var(--ink);font-weight:400}
.util .dot{display:inline-block;width:6px;height:6px;background:var(--red);border-radius:50%;margin:0 2px -1px 4px}

/* nav */
.nav{left:84px;top:80px;width:612px;height:25px;display:flex;gap:3px}
.nav a{flex:auto;background:var(--nav);color:#fff;font-family:"Gudea",sans-serif;font-size:9px;display:flex;align-items:center;justify-content:center}

/* sidebar */
.browse{left:84px;top:118px;width:121px}
.browse h3{background:var(--red);color:#fff;font-size:9px;font-weight:400;height:21px;line-height:21px;padding-left:11px;border:1px solid var(--red-dark)}
.browse li{list-style:none;height:19px;border:1px solid #e4e4e4;border-top:0;font-size:6.5px;color:#444;display:flex;justify-content:space-between;align-items:center;padding:0 8px 0 9px}
.browse li span{font-size:9px;color:#666}

/* hero */
.hero{left:214px;top:118px;width:481px;height:173px;background:linear-gradient(160deg,#b08d6e 0%,#e6d6c0 32%,#c02a1c 60%,#8c1b12 100%)}
.hero-title{left:222px;top:244px;font-family:"Gudea",sans-serif;font-weight:700;font-size:17.5px;line-height:17px;color:var(--ink)}
.cta{left:583px;top:131px;width:117px;height:83px;background:var(--red);color:#fff;padding:9px 12px;font-family:"Gudea",sans-serif;font-weight:700;font-size:14px;line-height:15.5px;border:1px solid #fff}
.cta small{display:block;text-align:right;font-size:7px;margin-top:5px}
.savings{left:583px;top:227px;width:117px;height:46px;background:var(--nav);color:#fff;padding:9px 0 0 17px;font-family:"Gudea",sans-serif;font-weight:700;font-size:11px;line-height:12px}
.savings i{position:absolute;right:8px;bottom:3px;font-style:normal;font-size:8px}

/* promos */
.promo{left:84px;width:121px;border:1px solid #ccc;padding:3px}
.promo .fill{width:100%;height:100%}
.promo-off{top:312px;height:110px}
.promo-off .fill{background:linear-gradient(135deg,#e8e8e8,#f6f6f6 50%,#dedede)}
.promo-off p{position:absolute;left:14px;top:30px;font-family:"Gudea",sans-serif;font-size:15px;line-height:16.5px;color:#555}
.promo-off p em{font-style:normal;color:var(--red)}
.promo-floor{top:436px;height:72px}
.promo-floor .fill{background:linear-gradient(180deg,#c89b61,#2d2a4a 45%,#6a3b2c)}
.promo-floor span{position:absolute;left:0;right:0;bottom:8px;text-align:center;color:#fff;font-family:"Gudea",sans-serif;font-weight:700;font-size:11px}

.sec-head{font-family:"Gudea",sans-serif;font-weight:700;font-size:9.5px;color:#333;display:flex;align-items:center;gap:12px}
.sec-head::after{content:"";flex:1;border-top:3px double var(--line)}
.sec-head .arrows{order:2;font-size:10px;color:#222;letter-spacing:1px}
.like-head{left:216px;top:309px;width:478px}
.collection{top:334px;width:232px}
.collection .fill{height:88px}
.c1{left:214px}.c1 .fill{background:linear-gradient(135deg,#5e2b7a,#8e4aa8 50%,#4a1f66)}
.c2{left:462px}.c2 .fill{background:linear-gradient(135deg,#6e1a14,#b2341f 50%,#c99a52)}
.collection h4{font-family:"Gudea",sans-serif;font-size:10px;color:var(--ink);margin:13px 0 8px;font-weight:700}
.collection h4 b{color:var(--red);margin-left:5px}
.collection p{font-size:7px;line-height:11px;color:#666}

/* products */
.row-head{left:84px;width:612px}
.cards{left:84px;width:612px;display:flex;gap:13px}
.card{flex:1;height:171px;border:1px solid #e4e4e4;box-shadow:0 3px 3px -2px #bbb;padding:6px}
.card .fill{height:98px}
.card .name{font-size:8px;color:#666;margin:18px 0 0 7px}
.feat .buy{display:flex;align-items:flex-start;gap:16px;margin:8px 0 0 9px}
.btn-red{background:var(--red);color:#fff;font-size:6px;font-weight:700;padding:5px 5px;border-radius:2px}
.price-old{font-size:8px;color:#777;text-decoration:line-through;line-height:9px}
.price-new{font-size:8px;color:var(--red);line-height:9px}
.best .name{text-align:center;margin:7px 0 0}
.best .price{text-align:center;font-weight:700;color:var(--red);font-size:11px;margin-top:6px}
.btn-dark{margin:7px auto 0;width:87px;height:15px;background:var(--nav);color:#fff;font-size:7.5px;display:flex;align-items:center;justify-content:space-between;padding:0 5px 0 12px}
.btn-dark b{font-size:11px}

/* footer */
.footer{left:84px;top:966px;width:612px;height:234px;background:var(--panel)}
.fcol{position:absolute;top:18px}
.fcol h5{font-family:"Gudea",sans-serif;font-size:9px;color:#333;margin-bottom:23px}
.fcol li{list-style:none;font-size:7.5px;color:#444;line-height:12.4px}
.frule{position:absolute;left:17px;right:17px;top:38px;border-top:1px solid var(--line)}
.pays{display:flex;gap:3px}
.pays i{width:20px;height:13px;border:1px solid #bbb;background:#fff}
.pays i:nth-child(odd){background:#e9eef7}
.badges{display:flex;gap:6px;margin-top:20px;align-items:center}
.badges i{display:block;background:#d8d8d8;border:1px solid #bbb}
.copy{position:absolute;left:0;right:0;bottom:0;height:34px;background:var(--dark);color:#aaa;font-size:7.5px;display:flex;align-items:center;justify-content:center}
</style>
</head>
<body>

<header>
  <div class="abs brand"><span class="brand-mark"></span><span class="brand-name">FloorNest.com</span></div>
  <div class="abs brand-tag">for domestic and heirloom values</div>
  <form class="abs search"><input value="Enter a keyword or item" aria-label="Search"><button type="button" aria-label="Search">
    <svg width="11" height="11" viewBox="0 0 12 12"><circle cx="5" cy="5" r="3.6" fill="none" stroke="#fff" stroke-width="1.6"/><path d="M7.7 7.7 11 11" stroke="#fff" stroke-width="1.6"/></svg></button></form>
  <div class="abs util">
    <div>Items (0) &nbsp;<b style="color:#222;font-weight:400">Total $0.00</b> &nbsp;View Cart &nbsp;|&nbsp; Checkout</div>
    <div class="tel">Order Toll-Free &nbsp;: &nbsp;<b>1-888-555-0142</b></div>
    <div>My Account &nbsp;|&nbsp; Sign <span class="dot"></span>Live Chat <span class="dot"></span>Online</div>
  </div>
  <nav class="abs nav">
    <a>Home</a><a>Selection Guides</a><a>Rug Care</a><a>Faq</a><a>Return Policy</a><a>Free Shipping</a><a>Return Policy</a>
  </nav>
</header>

<aside class="abs browse">
  <h3>BROWSE</h3>
  <ul>
    <li>RUG THEME<span>+</span></li><li>COLOR WAY<span>+</span></li><li>SIZE<span>+</span></li><li>SHAPE<span>+</span></li>
    <li>FIBER CONTENT<span>+</span></li><li>MFGR. BRAND<span>+</span></li><li>MFGR.COLLECTION<span>+</span></li><li>PRICE<span>+</span></li>
  </ul>
</aside>

<section>
  <div class="abs hero" role="img" aria-label="Close-up photo of shaggy cream and red area rugs"></div>
  <h1 class="abs hero-title">For Domestic and<br>Heirloom values</h1>
  <a class="abs cta">GREAT RUGS<br>FOR HOME<br>DECORATORS<small>Shop Now &nbsp;›</small></a>
  <a class="abs savings">HUGE SAVINGS<br>ON HOME RUGS<i>›</i></a>
</section>

<div class="abs promo promo-off"><div class="fill" role="img" aria-label="Soft white shag rug texture"></div><p><em>30% OFF ON</em><br>COMFORTABLE<br><em>RUGS</em></p></div>
<div class="abs promo promo-floor"><div class="fill" role="img" aria-label="Patterned navy floor rug on wooden floor"></div><span>FLOOR RUGS</span></div>

<h2 class="abs sec-head like-head">YOU MAY ALSO LIKE</h2>
<article class="abs collection c1">
  <div class="fill" role="img" aria-label="Purple geometric rug"></div>
  <h4>Hearthside Collection<b>›</b></h4>
  <p>Lorem Ipsum is simply dummy text of the printing and typesetting industry. Lorem Ipsum has been the industry's standard dummy text ever since the 1500s, when an unknown printer took a galley of type and scrambled it to make a type specimen book.</p>
</article>
<article class="abs collection c2">
  <div class="fill" role="img" aria-label="Red and gold floral rose rug"></div>
  <h4>Workspace Weave Collection<b>›</b></h4>
  <p>Lorem Ipsum is simply dummy text of the printing and typesetting industry. Lorem Ipsum has been the industry's standard dummy text ever since the 1500s, when an unknown printer took a galley of type and scrambled it to make a type specimen book.</p>
</article>

<h2 class="abs sec-head row-head" style="top:526px">FEATURED RUGS<span class="arrows">‹ ›</span></h2>
<div class="abs cards feat" style="top:554px">
  <div class="card"><div class="fill" role="img" aria-label="Brown rug with colourful circles" style="background:linear-gradient(135deg,#3a2418,#c0392b 45%,#e3c14b 60%,#2a1a12)"></div><p class="name">Lorem Ipsum Dolor</p><div class="buy"><span class="btn-red">ADD TO CART</span><div><div class="price-old">$55.67</div><div class="price-new">$48.67</div></div></div></div>
  <div class="card"><div class="fill" role="img" aria-label="Grey striped rug in a bright living room" style="background:linear-gradient(180deg,#e4e4e4,#9a9a9a 55%,#cfcfcf)"></div><p class="name">Lorem Ipsum Dolor</p><div class="buy"><span class="btn-red">ADD TO CART</span><div><div class="price-old">$55.67</div><div class="price-new">$48.67</div></div></div></div>
  <div class="card"><div class="fill" role="img" aria-label="Cream rug with black and red border" style="background:radial-gradient(ellipse at center,#eee6d6 45%,#8b2a1c 60%,#2a1c18)"></div><p class="name">Lorem Ipsum Dolor</p><div class="buy"><span class="btn-red">ADD TO CART</span><div><div class="price-old">$55.67</div><div class="price-new">$48.67</div></div></div></div>
  <div class="card"><div class="fill" role="img" aria-label="Grey striped rug in a bright living room" style="background:linear-gradient(180deg,#e4e4e4,#9a9a9a 55%,#cfcfcf)"></div><p class="name">Lorem Ipsum Dolor</p><div class="buy"><span class="btn-red">ADD TO CART</span><div><div class="price-old">$55.67</div><div class="price-new">$48.67</div></div></div></div>
</div>

<h2 class="abs sec-head row-head" style="top:746px">BEST QUALITY RUGS<span class="arrows">‹ ›</span></h2>
<div class="abs cards best" style="top:774px">
  <div class="card"><div class="fill" role="img" aria-label="Pale patterned rug in a room with a chair" style="background:linear-gradient(180deg,#b89a78,#ddd2c0 50%,#a47a52)"></div><p class="name">Lorem Ipsum Dolor Sit</p><p class="price">$5.91</p><div class="btn-dark">Add to Cart<b>+</b></div></div>
  <div class="card"><div class="fill" role="img" aria-label="White shag rug with red waves beside a sofa" style="background:linear-gradient(180deg,#a33 0%,#e8e4df 45%,#9c3026 75%,#ddd)"></div><p class="name">Lorem Ipsum Dolor Sit</p><p class="price">$5.91</p><div class="btn-dark">Add to Cart<b>+</b></div></div>
  <div class="card"><div class="fill" role="img" aria-label="Red rug in a bright room" style="background:linear-gradient(180deg,#efe9e0,#c0281c 55%,#8c1a12)"></div><p class="name">Lorem Ipsum Dolor Sit</p><p class="price">$5.91</p><div class="btn-dark">Add to Cart<b>+</b></div></div>
  <div class="card"><div class="fill" role="img" aria-label="Navy patterned rug on wooden floor" style="background:linear-gradient(180deg,#c89b61,#2d2a4a 45%,#7a3b2c)"></div><p class="name">Lorem Ipsum Dolor Sit</p><p class="price">$5.91</p><div class="btn-dark">Add to Cart<b>+</b></div></div>
</div>

<footer class="abs footer">
  <div class="frule"></div>
  <div class="fcol" style="left:17px"><h5>Customer Services</h5><ul><li>Shipping</li><li>Return Policy</li><li>Privacy Policy</li><li>Ordering &amp; Delivery</li><li>Checklist</li><li>Terms of Use</li><li>Terms of Sale</li><li>Contact Us</li><li>Environmental Policy</li></ul></div>
  <div class="fcol" style="left:143px"><h5>Resources</h5><ul><li>Product Articles</li><li>Learning Center</li><li>Help</li><li>Refer A Friend</li><li>FloorNest Blog</li><li>Room Scene Viewer</li><li>Site Map</li><li>FAQ</li><li>Customer Testimonials</li><li>Photo Gallery</li></ul></div>
  <div class="fcol" style="left:261px"><h5>Corporate Info</h5><ul><li>About FloorNest.com</li><li>Careers</li><li>Affiliates</li></ul></div>
  <div class="fcol" style="left:389px"><h5>Payments &amp; Security</h5>
    <div class="pays"><i></i><i></i><i></i><i></i><i></i><i style="width:80px;border:0;background:#dfe6f2"></i></div>
    <div class="badges"><i style="width:28px;height:28px;border-radius:50%"></i><i style="width:28px;height:28px;border-radius:50%"></i><i style="width:40px;height:16px"></i><i style="width:40px;height:20px"></i><i style="width:50px;height:16px"></i></div>
  </div>
  <div class="copy">© Copyrights 2013 FloorNest. All rights Reserved</div>
</footer>

</body>
</html>
```